business card deign

Logo needs the following on it.
1. attached logo
2. Tagline - "If it keeps the cooler full or the night rolling...we got it!"
3. Name- Dalton Pikes, Founder and CPO
4. Address - 412 E. Carver Avenue, Ste 2207, Tampa, FL. 33917
5. Phone - 555.318.4726

```html
<!DOCTYPE html>
<html lang="en">
<head>
<meta charset="utf-8">
<title>Hopwell Business Card</title>
<link rel="stylesheet" href="https://fonts.googleapis.com/css2?family=Montserrat:wght@400;700;800&display=swap">
<style>
  :root {
    --stage: #2e2e2e;
    --card: #242424;
    --card-edge: #1b1b1b;
    --ink: #ffffff;
    --ink-soft: #e6e6e6;
    --pattern-dark: #1e1e1e;
    --pattern-light: #4a4a4a;
  }
  * { box-sizing: border-box; margin: 0; padding: 0; }
  html, body { width: 1200px; height: 900px; overflow: hidden; }
  body {
    background: var(--stage);
    font-family: "Montserrat", sans-serif;
    color: var(--ink);
    display: flex;
    flex-direction: column;
    align-items: center;
    justify-content: center;
    gap: 56px;
  }
  .card {
    position: relative;
    width: 600px;
    height: 343px;
    background: var(--card);
    border-radius: 22px;
    overflow: hidden;
    box-shadow: 0 14px 30px rgba(0,0,0,0.45);
  }

  /* Front */
  .card-front { display: flex; align-items: center; }
  .front-brand {
    width: 290px;
    display: flex;
    justify-content: center;
  }
  .wordmark {
    font-weight: 800;
    letter-spacing: 0.42em;
    color: var(--ink);
    text-transform: uppercase;
    white-space: nowrap;
  }
  .front-brand .wordmark { font-size: 30px; margin-right: -0.42em; }
  .divider {
    width: 1px;
    height: 150px;
    background: var(--ink-soft);
  }
  .contact { padding-left: 32px; }
  .contact-name {
    font-size: 23px;
    font-weight: 800;
    text-transform: uppercase;
    letter-spacing: 0.02em;
  }
  .contact-role { font-size: 14px; margin-top: 2px; color: var(--ink-soft); }
  .contact-address { font-size: 14px; line-height: 1.45; margin-top: 16px; }
  .contact-line {
    display: flex;
    align-items: center;
    gap: 8px;
    font-size: 14px;
    margin-top: 6px;
  }
  .contact-address + .contact-line { margin-top: 10px; }
  .contact-line svg { width: 12px; height: 12px; flex: none; }

  /* Back */
  .back-pattern {
    position: absolute;
    inset: 0;
    background: linear-gradient(115deg, var(--pattern-dark) 0%, #2b2b2b 45%, var(--pattern-light) 100%);
  }
  .back-content {
    position: relative;
    height: 100%;
    display: flex;
    flex-direction: column;
    align-items: center;
    justify-content: center;
    gap: 22px;
  }
  .back-content .wordmark { font-size: 34px; margin-right: -0.42em; }
  .tagline { font-size: 16px; font-weight: 400; letter-spacing: 0.01em; white-space: nowrap; }
</style>
</head>
<body>

  <section class="card card-front">
    <div class="front-brand">
      <span class="wordmark">Hopwell</span>
    </div>
    <div class="divider"></div>
    <div class="contact">
      <p class="contact-name">Dalton Pikes</p>
      <p class="contact-role">Founder and CPO</p>
      <p class="contact-address">412 E. Carver Avenue<br>Ste 2207, Tampa, FL. 33917</p>
      <p class="contact-line">
        <svg viewBox="0 0 12 12" aria-hidden="true"><path fill="#fff" d="M2.4 1l2 2.2-1 1.3a7 7 0 0 0 4.1 4.1l1.3-1 2.2 2-1 1.4C6 11 1 6 .9 2z"/></svg>
        555.318.4726
      </p>
      <p class="contact-line">
        <svg viewBox="0 0 12 12" aria-hidden="true"><rect x="0.5" y="2" width="11" height="8" rx="1" fill="none" stroke="#fff"/><path d="M1 2.6l5 4 5-4" fill="none" stroke="#fff"/></svg>
        dalton@hopwellgear.com
      </p>
    </div>
  </section>

  <section class="card card-back">
    <div class="back-pattern" role="img" aria-label="Repeating tone-on-tone pattern of the brand symbol across the card"></div>
    <div class="back-content">
      <span class="wordmark">Hopwell</span>
      <p class="tagline">If it keeps the cooler full or the night rolling...we got it!</p>
    </div>
  </section>

</body>
</html>
```